Small Business Directory Site Requires a Professional Responsive Web Design

Small Business Directory and Coupon Site - we require a complete website design for a brand new responsive & mobile friendly website. We already have a coder who will professional code our website in Magento.

All PSD pages need to be professionally designed then uploaded into a sharedrive (i.e. like filecrate). Additionally, as I cannot pre-empt everything, please note that we may require a little more assistance once the files have been transferred (for example, in www.brightlane-listings.example if you hover your mouse on the search box you will see a pop up box. We want one of these too and I think that means there may be extra design work here)

We have some draft page sketches have been created (there are some minor changes we want to the sketches provided though); however, we require an excellent designer to add the creative touches to it to make it look professionally created. All artwork/font must be legal.

-------------------------
We like the look of the www.brightlane-listings.example and www. marlowfolio.example

For the headers, please consider a font similar to RNS camellia. We likes this style, but it is too thin for the headers...so we need a variation like this one. For the copy/general text font, something basic that marries well with the headers.

---------------------

Please be sure to also read the brief we wrote for the coder as this will help with better understanding our design requirements.

In total I believe we have about 50 pages. This includes all the little pages and most of the pop up boxes (but not the little help key boxes). For example, pages include...

1. Login (this is where customers log in and can edit, manage their profiles. This means that there are backend membership pages)
2. Mini Services (same look and feel as the business coupons)
3. Resource Centre
4. Join (this is where customers learn about the packages available to submit a directory listing, if they ‘buy’ a package (i.e. free, $25 or $150 package) then they can create their own directory listing)
5. Search the directory (customer can view all the categories and also search the directory)
6. Create a directory listing (this is where customers learn about the packages available to submit a directory listing, if they ‘buy’ a package (i.e. free, $25 or $150 package) then they can create their own directory listing)
7. Quote finder (also know as Get a Quote)
8. Coupons (customer go to the business coupon page and can view all current coupons/submit a coupon)
9. Submit a coupon (form)
10.Advertise with us (form)
11. Join the forum
12.Submit an article or video (form)
13. Affiliates (listing of affiliates we currently have)
14. Become an affiliate (form)
15. Case studies (customer can view the case studies we have in the resource centre)
16. Help Guides (customer can view the help guides we have in the resource centre)
17. About Us
18 .Contact Us (form)
19. Terms & Condition
20. Privacy Policy
21. Supporting City Councils
22. Site Map
23. Forgot password / login details
24. Homepage
25. If we hover over a few areas (i.e. search box, location field) it pops up with more information.
etc etc etc. . . there are more pages.

Please see our filecrate link for the draft mock up pages that I have created so far.

https://www.cloudtrunk.example/sh/qk72pmw4rtz8nd/KLMvbTq2fWndxPzs8Yh4ecRQu

We are in a rush! We'd like to get the majority of the artwork completed by the end of the month. Minor fixes/tweaks can occur thereafter.

Target Market(s)

Small Businesses (employees 0 - 50) located throughout Australia

Industry/Entity Type

Business

Font styles to use
Sans Serif

Requirements
Must have
• Professional. Artwork must be legal (cannot be cut and paste or taken off other websites, must be legally purchased and used).Must look contemporary, fresh, modern.

Absolutely must be a responsive site!
Nice to have
• original work, original photos, original art.

like modern, fresh photos that demonstrate innovation, growth, small business, Australian scenery, stability, goals/passion.
Should not have
• cut and paste graphics, illegal graphics, not purchased graphics.

```html
<!DOCTYPE html>
<html lang="en">
<head>
<meta charset="utf-8">
<title>Tradeway Link – Small Business Directory</title>
<link rel="stylesheet" href="https://fonts.googleapis.com/css2?family=Archivo:wght@700;800&family=Noto+Sans:wght@400;700&display=swap">
<style>
:root{
  --orange:#f47a20;
  --black:#000;
  --footer:#141414;
  --text:#444;
  --white:#fff;
  --band:#efefef;
  --panel:rgba(10,8,6,.88);
}
*{box-sizing:border-box;margin:0;padding:0}
html,body{width:997px;height:1200px;overflow:hidden;background:var(--white)}
body{position:relative;font-family:"Noto Sans",Verdana,sans-serif;color:var(--text)}
.head-font{font-family:"Archivo",Arial,sans-serif;font-weight:800}
.abs{position:absolute}

.site-header{left:0;top:0;width:997px;height:98px;background:var(--black)}
.brand{left:110px;top:30px;display:flex;align-items:center;gap:10px}
.brand-square{width:34px;height:34px;background:var(--orange)}
.brand-name{color:var(--white);font-family:"Archivo",Arial,sans-serif;font-weight:700;font-size:22px;letter-spacing:.5px}
.search-bar{left:405px;top:26px;width:368px;height:48px;background:var(--orange);padding:8px;display:flex;gap:8px}
.search-field{background:var(--white);height:32px;font-size:11.5px;color:#333;padding:8px 9px}
.search-field.what{width:148px}
.search-field.where{width:148px}
.search-go{width:39px;height:32px;background:var(--white);display:flex;align-items:center;justify-content:center}
.top-nav{top:40px;color:var(--white);font-size:13px;letter-spacing:.5px}

.hero{left:0;top:98px;width:997px;height:316px;background:linear-gradient(180deg,#4a2c10 0%,#8a4a12 35%,#d07a1c 60%,#7a3e12 85%,#2a1a10 100%)}
.hero-title{left:109px;top:138px;color:var(--white);font-size:39px;letter-spacing:.3px}
.hero-sub{left:109px;top:196px;color:var(--white);font-size:21.5px}
.btn{background:var(--orange);color:var(--white);display:flex;align-items:center;justify-content:center}
.hero-btn{left:109px;top:244px;width:157px;height:42px;font-family:"Archivo",Arial,sans-serif;font-weight:700;font-size:18px}
.dots{left:456px;top:375px;display:flex;gap:7px}
.dot{width:13px;height:13px;border-radius:50%;background:var(--orange);border:2px solid var(--white)}
.dot.active{background:var(--black)}
.directory{left:673px;top:116px;width:214px;height:277px;background:var(--panel);padding:20px 22px}
.directory h2{color:var(--white);font-size:22px;margin-bottom:8px}
.directory p{color:var(--white);font-size:11.5px;line-height:21.7px}
.directory .btn{margin-top:17px;width:170px;height:37px;font-weight:700;font-size:13.5px}

.community-title{left:0;top:432px;width:997px;text-align:center;color:var(--orange);font-size:28.5px}
.card{top:489px;width:232px}
.card-media{width:232px;height:165px;box-shadow:0 1px 4px rgba(0,0,0,.45);border:2px solid #fff;display:flex;align-items:center;justify-content:center}
.media-office{background:linear-gradient(135deg,#e9eef2,#c9b8a4 55%,#eef1f4)}
.media-desk{background:linear-gradient(135deg,#dfe6ea,#b9c4cc 50%,#f1efe9)}
.media-partner{background:#efefef;color:#1d3a5c;font-family:"Noto Sans",sans-serif;font-weight:700;font-size:28px}
.card h3{margin-top:18px;color:var(--orange);font-family:"Noto Sans",sans-serif;font-weight:700;font-size:14px}
.card p{margin-top:5px;font-size:12px;line-height:22px;color:var(--text)}
.card a{display:block;margin-top:3px;color:var(--orange);font-weight:700;font-size:14px;text-decoration:underline}

.partners{left:0;top:849px;width:997px;height:92px;background:var(--band)}
.partner-name{top:30px;font-family:"Noto Sans",sans-serif;font-weight:700;font-size:30px;color:#1e1e1e}

.site-footer{left:0;top:941px;width:997px;height:259px;background:var(--footer)}
.foot-col{top:966px}
.foot-col h4{color:var(--orange);font-size:19px;margin-bottom:14px}
.foot-col li{list-style:none;color:var(--white);font-size:12px;line-height:22px}
.social{left:752px;top:1011px;display:flex;gap:12px}
.social span{width:24px;height:24px;border-radius:50%}
.copyright{left:0;top:1155px;width:997px;text-align:center;color:var(--white);font-size:12px}
</style>
</head>
<body>

<header class="abs site-header">
  <div class="abs brand"><span class="brand-square"></span><span class="brand-name">TRADEWAY LINK</span></div>
  <form class="abs search-bar">
    <div class="search-field what">What do you find?</div>
    <div class="search-field where">Chennai , 25</div>
    <div class="search-go">
      <svg width="18" height="18" viewBox="0 0 18 18"><circle cx="7" cy="7" r="5.2" fill="none" stroke="#f47a20" stroke-width="2.4"/><line x1="11" y1="11" x2="16" y2="16" stroke="#f47a20" stroke-width="2.8" stroke-linecap="round"/></svg>
    </div>
  </form>
  <span class="abs top-nav" style="left:795px">LOGIN</span>
  <span class="abs top-nav" style="left:858px">JOIN</span>
</header>

<section class="abs hero" role="img" aria-label="Sunset sky over the horizon with birds in flight"></section>
<h1 class="abs hero-title head-font">LET US HELP YOU GROW</h1>
<p class="abs hero-sub head-font">AUSTRALIA’S SMALL BUSINESS SUPPORT LINK</p>
<a class="abs btn hero-btn">Join Us Today</a>
<div class="abs dots"><span class="dot active"></span><span class="dot"></span><span class="dot"></span><span class="dot"></span><span class="dot"></span></div>
<aside class="abs directory">
  <h2 class="head-font">DIRECTORY</h2>
  <p>Our small business directory is maintained to give members choice. We’re open to all busi-nesses, regardless of your location, so long as they ser-vice Australian small busi-nesses.</p>
  <a class="btn">Create Your free listing</a>
</aside>

<h2 class="abs community-title head-font">GET REAL SUPPORT FROM OUR COMMUNITY</h2>

<article class="abs card" style="left:109px">
  <div class="card-media media-office" role="img" aria-label="Smiling businesswoman with her team in an office"></div>
  <h3>How Did You Sort Your Business?</h3>
  <p>Learn from Mara Tilden, a real small business owner. How she started her business and what are the most valuable resources for her right now.</p>
  <a>Case Study</a>
</article>
<article class="abs card" style="left:382px">
  <div class="card-media media-desk" role="img" aria-label="Two colleagues working at a desk, video preview">
    <svg width="32" height="30" viewBox="0 0 32 30"><rect width="32" height="30" rx="5" fill="#e3241b"/><polygon points="12,8 23,15 12,22" fill="#fff"/></svg>
  </div>
  <h3>Why Go with Tradeway Link?</h3>
  <p>What small business owner can’t relate to the ongoing task of attracting new cus-tomers? Struggling with cash flow? Or how about not having enough time.</p>
  <a>Our Whiteboard Video</a>
</article>
<article class="abs card" style="left:654px">
  <div class="card-media media-partner">Harbour Cover</div>
  <h3>Become an Affiliate</h3>
  <p>If you have a network of small busi-nesses, let us help to create additional value for your members and make money for your network. Talk to us today.</p>
  <a>Our Whiteboard Video</a>
</article>

<section class="abs partners">
  <span class="abs partner-name" style="left:109px">Fieldgrain</span>
  <span class="abs partner-name" style="left:440px">Deskharbor</span>
  <span class="abs partner-name" style="left:742px">Northwire</span>
</section>

<footer class="abs site-footer"></footer>
<nav class="abs foot-col" style="left:109px"><h4 class="head-font">SITE DIRECTORY</h4><ul><li>Search the directory</li><li>Create a directory listing</li><li>Quote finder</li><li>Coupons</li><li>Submit a coupon</li><li>Advertise with us</li></ul></nav>
<nav class="abs foot-col" style="left:298px"><h4 class="head-font">RESOURCES</h4><ul><li>Join the forum</li><li>Submit an article or video</li><li>Affiliates</li><li>Become an affiliate</li><li>case studies</li><li>Help guides</li></ul></nav>
<nav class="abs foot-col" style="left:471px"><h4 class="head-font">CATEGORIES</h4><ul><li>Join the forum</li><li>Submit an article</li><li>Affiliates</li><li>Become an affiliate</li><li>case studies</li><li>Help guides</li></ul></nav>
<nav class="abs foot-col" style="left:627px"><h4 class="head-font">ABOUT</h4><ul><li>About us</li><li>Contact us</li><li>Terms &amp; conditions</li><li>Privacy policy</li><li>Support</li><li>Site map</li></ul></nav>
<div class="abs foot-col" style="left:751px"><h4 class="head-font">FOLLOW US</h4></div>
<div class="abs social" aria-label="Social links">
  <span style="background:#5bb8e8"></span><span style="background:#e05a5a"></span><span style="background:#4a6fb5"></span><span style="background:#555"></span>
</div>
<p class="abs copyright">Copyright @ 2014 Tradewaylink.All Rights Reserved.</p>

</body>
</html>
```